Business Card for Vorla Parts Wholesale supplier

Hi There! I need a new business card for our company. We are specialized in selling Vorla parts, mostly we sell new LCD screens for Zelnar and Drelks. I would like to see that back in the design.

You can find the colors and logo's on our website: www.hartuvo.nl

Industry/Entity Type

Business

Contact Information for Business Card

My Details:
Tobias Lindqvist

Phone: 0031687203316
E-mail: Tobias@hartuvo.nl

Slogan: "Because Quality Matters"

Font styles to use
Sans Serif

Colors

Designer to choose colors to be used in the design.

Requirements
Must have
• A Black backside with the Hartuvo logo on it. The front side should be clean with only my contact details.
• But I'm also open for something really different or awesome!
Nice to have
• Remember that we are in the parts & repairing industry, So i'll be handing those business cards mainly to repair companies. Maybe you can do something with that thought :)

```html
<!DOCTYPE html>
<html lang="en">
<head>
<meta charset="utf-8">
<title>Hartuvo Business Card</title>
<link href="https://fonts.googleapis.com/css2?family=Exo+2:wght@400;600;700&display=swap" rel="stylesheet">
<style>
  :root {
    --orange: #f37321;
    --orange-soft: #f58a45;
    --card-grey: #e6e6e6;
    --ink: #1a1a1a;
    --text-grey: #333333;
    --white: #ffffff;
    --backdrop: #f2f0ee;
  }
  html, body {
    margin: 0;
    padding: 0;
    overflow: hidden;
  }
  .canvas {
    position: relative;
    width: 1200px;
    height: 900px;
    background: var(--backdrop);
    font-family: "Exo 2", sans-serif;
    overflow: hidden;
  }
  .card {
    position: absolute;
    border-radius: 18px;
    overflow: hidden;
    box-shadow: 0 6px 18px rgba(0, 0, 0, 0.12);
  }
  .card-front {
    left: 237px;
    top: 60px;
    width: 555px;
    height: 345px;
    background: var(--card-grey);
  }
  .front-band {
    position: absolute;
    inset: 0;
  }
  .brand {
    position: absolute;
    left: 31px;
    top: 30px;
    display: flex;
    align-items: center;
    gap: 12px;
  }
  .brand-square {
    width: 58px;
    height: 58px;
    background: var(--orange);
    border-radius: 6px;
  }
  .brand-name {
    font-weight: 700;
    font-size: 58px;
    line-height: 1;
    color: var(--ink);
    letter-spacing: 0.5px;
  }
  .holder-name {
    position: absolute;
    left: 31px;
    top: 198px;
    margin: 0;
    font-weight: 700;
    font-size: 24px;
    letter-spacing: 0.5px;
    color: var(--orange);
  }
  .contact-list {
    position: absolute;
    left: 31px;
    top: 242px;
    margin: 0;
    padding: 0;
    list-style: none;
  }
  .contact-item {
    display: flex;
    align-items: center;
    gap: 8px;
    height: 25.5px;
    font-size: 15px;
    color: var(--text-grey);
  }
  .contact-icon {
    width: 16px;
    height: 16px;
    flex: none;
  }
  .slogan {
    position: absolute;
    left: 299px;
    top: 291px;
    margin: 0;
    font-size: 17px;
    color: var(--white);
    letter-spacing: 0.2px;
  }
  .card-back {
    left: 458px;
    top: 518px;
    width: 559px;
    height: 344px;
    background: var(--orange);
    display: flex;
    align-items: center;
    justify-content: center;
  }
  .back-texture {
    position: absolute;
    inset: 0;
    background: radial-gradient(circle at 50% 50%, var(--orange) 0%, var(--orange-soft) 120%);
  }
  .back-brand {
    position: relative;
    font-weight: 700;
    font-size: 82px;
    line-height: 1;
    color: var(--white);
    letter-spacing: 1px;
  }
</style>
</head>
<body>
<div class="canvas">

  <section class="card card-front" aria-label="Business card front">
    <svg class="front-band" width="555" height="345" viewBox="0 0 555 345" aria-hidden="true">
      <polygon points="448,0 555,0 555,345 251,345" fill="var(--orange)"/>
      <circle cx="433" cy="206" r="96" fill="var(--white)" opacity="0.12"/>
    </svg>

    <div class="brand">
      <span class="brand-square" aria-hidden="true"></span>
      <span class="brand-name">hartuvo</span>
    </div>

    <h1 class="holder-name">TOBIAS LINDQVIST</h1>

    <ul class="contact-list">
      <li class="contact-item">
        <svg class="contact-icon" viewBox="0 0 16 16" aria-hidden="true">
          <circle cx="8" cy="8" r="8" fill="var(--orange)"/>
          <path d="M4.5 9.5c0-2.5 1.5-4 3.5-4s3.5 1.5 3.5 4h-2V8.5h-3v1z" fill="var(--white)"/>
        </svg>
        <span>0031687203316</span>
      </li>
      <li class="contact-item">
        <svg class="contact-icon" viewBox="0 0 16 16" aria-hidden="true">
          <circle cx="8" cy="8" r="8" fill="var(--orange)"/>
          <rect x="4" y="5.2" width="8" height="5.6" fill="var(--white)"/>
          <path d="M4 5.2l4 3 4-3" fill="none" stroke="var(--orange)" stroke-width="0.9"/>
        </svg>
        <span>Tobias@hartuvo.nl</span>
      </li>
      <li class="contact-item">
        <svg class="contact-icon" viewBox="0 0 16 16" aria-hidden="true">
          <circle cx="8" cy="8" r="8" fill="var(--orange)"/>
          <circle cx="8" cy="8" r="4" fill="none" stroke="var(--white)" stroke-width="1.2"/>
          <path d="M4 8h8M8 4c-1.6 2.4-1.6 5.6 0 8M8 4c1.6 2.4 1.6 5.6 0 8" fill="none" stroke="var(--white)" stroke-width="0.9"/>
        </svg>
        <span>www.hartuvo.nl</span>
      </li>
    </ul>

    <p class="slogan">Because Quality Matters</p>
  </section>

  <section class="card card-back" aria-label="Business card back">
    <div class="back-texture" role="img" aria-label="Orange background texture"></div>
    <span class="back-brand">hartuvo</span>
  </section>

</div>
</body>
</html>
```